UX - Need some screens design for a Skill Assessment Application

I am building an app to carry out skill assessments. Depending on how the assessment is configured, it may have one or more parts
1. Question based assessment (Multiple Choice, True False, Fill in the blanks"
2. Endorsement by two colleagues - A screen that allows user to pick colleagues based on search and shows the status of pending requests
3. A written submission - a page that explains the format of the submission and a file upload
As each assessment can be configured with or without any of the steps, the assessment UI must be such that these areas get hidden/displayed based on configuration.
Colour codes to be used can be #0e78bb and #ffffff
There will also be a start screen (instructions) and an end screen (results)
Target Market(s)
Enterprise software
Number of Pages Required
4 page

```html
<!DOCTYPE html>
<html lang="en">
<head>
<meta charset="utf-8">
<title>Skill Assessment – Quiz</title>
<link href="https://fonts.googleapis.com/css2?family=Inter:wght@400;500;600;700&display=swap" rel="stylesheet">
<style>
:root{
  --nav:#0555ac;
  --primary:#0e78bb;
  --link:#1a8fd0;
  --ink:#1d1f22;
  --muted:#5d6166;
  --faint:#a3a7ab;
  --line:#dfe2e6;
  --band:#f6f7f9;
  --chip:#eceef0;
  --opt-num:#cfe9f6;
  --opt-sel:#e8f5fc;
  --teal:#0b9598;
  --white:#ffffff;
}
*{box-sizing:border-box;margin:0;padding:0}
html,body{width:1200px;height:771px;overflow:hidden;background:var(--white);font-family:'Inter',sans-serif;color:var(--ink)}
.abs{position:absolute}
.topbar{position:absolute;left:0;top:0;width:1200px;height:44px;background:var(--nav)}
.brand{position:absolute;left:70px;top:11px;display:flex;align-items:center;gap:10px;color:var(--white);font-size:14px;font-weight:600}
.brand-dot{width:20px;height:20px;border-radius:50%;background:#5cc3ee}
.nav-item{position:absolute;top:14px;font-size:12.5px;color:#cfe2f5}
.nav-item.active{color:var(--white);font-weight:700}
.nav-underline{position:absolute;left:487px;top:41px;width:80px;height:3px;background:#35b6e9}
.avatar{position:absolute;left:1099px;top:8px;width:28px;height:28px;border-radius:50%;background:linear-gradient(135deg,#7a5a4e,#2f3c52)}
.crumb{position:absolute;top:68px;font-size:11.5px}
.page-title{position:absolute;left:122px;top:98px;font-size:22px;font-weight:600;letter-spacing:-.2px}
.updated{position:absolute;right:90px;top:111px;font-size:11px;color:var(--muted)}
.band{position:absolute;left:0;top:140px;width:1200px;height:45px;background:var(--band);border-top:1px solid var(--line);border-bottom:1px solid var(--line)}
.meta{position:absolute;top:155px;font-size:10.5px;color:var(--ink)}
.meta b{font-weight:400;color:var(--link)}
.meta span{color:var(--muted)}
.sep{position:absolute;top:154px;width:1px;height:16px;background:#cdd1d5}
.chip{position:absolute;top:151px;height:24px;border-radius:12px;background:var(--chip);font-size:11.5px;color:var(--muted);display:flex;align-items:center;justify-content:center}
.step{position:absolute;left:88px;width:214px;height:43px;border:1px solid var(--line);border-radius:3px;font-size:12.5px;color:var(--faint);padding:0 16px;display:flex;align-items:center}
.step.active{border-color:var(--nav);color:var(--ink)}
.section-title{position:absolute;left:366px;top:219px;font-size:16px;font-weight:700}
.btn-outline{position:absolute;height:31px;border:1px solid var(--primary);border-radius:2px;color:var(--primary);font-size:11.5px;font-weight:500;display:flex;align-items:center;justify-content:center;background:var(--white)}
.rule{position:absolute;left:366px;top:254px;width:744px;height:1px;background:var(--line)}
.q-num{position:absolute;left:366px;top:272px;font-size:16px;color:var(--muted)}
.q-text{position:absolute;left:415px;top:272px;font-size:16px;font-weight:500}
.option{position:absolute;left:366px;width:467px;height:55px;border:1px solid var(--line);border-radius:2px;display:flex;align-items:center;font-size:12px;color:var(--muted)}
.option .n{width:31px;height:27px;margin:0 20px 0 13px;background:var(--opt-num);display:flex;align-items:center;justify-content:center;font-size:13px;color:var(--muted)}
.option.selected{border-color:var(--nav);background:var(--opt-sel);color:var(--nav)}
.progress-label{position:absolute;left:896px;top:280px;font-size:12.5px;color:var(--muted);display:flex;align-items:center;gap:8px}
.count{position:absolute;left:1088px;top:281px;font-size:10.5px;color:var(--muted)}
.count b{color:var(--ink);font-weight:600}
.note{position:absolute;left:896px;top:325px;width:214px;height:211px;background:var(--band);border-radius:4px;padding:20px 20px}
.note h3{font-size:15.5px;font-weight:500;margin-bottom:12px}
.note p{font-size:12px;line-height:20.6px;color:var(--muted)}
.percent{position:absolute;left:88px;top:664px;font-size:27px;font-weight:700}
.percent small{font-size:13px;font-weight:600}
.track{position:absolute;left:0;top:702px;width:1200px;height:7px;background:#f1f2f4}
.fill{position:absolute;left:0;top:702px;width:278px;height:7px;background:var(--teal)}
.skip{position:absolute;left:998px;top:731px;font-size:12px;color:var(--muted);display:flex;align-items:center;gap:4px}
.btn-primary{position:absolute;left:1058px;top:722px;width:52px;height:31px;background:var(--primary);color:var(--white);font-size:11.5px;font-weight:500;border-radius:2px;display:flex;align-items:center;justify-content:center}
</style>
</head>
<body>
<header class="topbar">
  <div class="brand"><div class="brand-dot"></div>Skillbase</div>
  <div class="nav-item active" style="left:487px">Assessments</div>
  <div class="nav-item" style="left:587px">Colleagues</div>
  <div class="nav-item" style="left:670px">Results</div>
  <div class="nav-underline"></div>
  <svg class="abs" style="left:1027px;top:13px" width="18" height="18" viewBox="0 0 24 24" fill="none" stroke="#fff" stroke-width="1.6"><path d="M6 17V11a6 6 0 0 1 12 0v6l2 2H4z"/><path d="M10 21h4"/></svg>
  <svg class="abs" style="left:1062px;top:13px" width="18" height="18" viewBox="0 0 24 24" fill="none" stroke="#fff" stroke-width="1.6"><circle cx="12" cy="12" r="3"/><path d="M12 2l2 3 3-1 1 3 3 1-1 3 2 2-2 2 1 3-3 1-1 3-3-1-2 3-2-3-3 1-1-3-3-1 1-3-2-2 2-2-1-3 3-1 1-3 3 1z"/></svg>
  <div class="avatar" role="img" aria-label="User profile photo"></div>
</header>

<svg class="abs" style="left:56px;top:65px" width="20" height="20" viewBox="0 0 20 20" fill="none" stroke="#1a8fd0" stroke-width="1.6"><circle cx="10" cy="10" r="9"/><path d="M14 10H6M9.5 6.5L6 10l3.5 3.5"/></svg>
<div class="crumb" style="left:88px;color:var(--link)">Assessment</div>
<div class="crumb" style="left:158px;color:var(--muted)">/ &nbsp;Application Design Capabilities</div>

<svg class="abs" style="left:88px;top:101px" width="22" height="22" viewBox="0 0 22 22" fill="none" stroke="#5d6166" stroke-width="1.5"><path d="M14 20H2V2h14v8"/><path d="M5 6h2M9 6h4M5 10h2M9 10h4M5 14h2"/><circle cx="16" cy="16" r="4"/><path d="M14.5 16l1 1 2-2"/></svg>
<h1 class="page-title">Application Design Capabilities</h1>
<div class="updated">Last Updated: <span style="color:var(--ink)">23/05/2024</span></div>

<div class="band"></div>
<div class="meta" style="left:88px">Assessment Date: <b>May 20, 2024</b></div>
<div class="sep" style="left:267px"></div>
<div class="meta" style="left:288px">Assessment Type: <b>UI/UX Skill</b></div>
<div class="sep" style="left:451px"></div>
<div class="meta" style="left:473px">Due Date: <span>24/05/2024</span></div>
<div class="chip" style="left:888px;width:42px">Quiz</div>
<div class="chip" style="left:936px;width:89px">Endorsement</div>
<div class="chip" style="left:1031px;width:79px">Submission</div>

<div class="step active" style="top:219px">Quiz</div>
<div class="step" style="top:271px">Endorsement</div>
<div class="step" style="top:322px">Submission</div>

<h2 class="section-title">Quiz</h2>
<div class="btn-outline" style="left:1006px;top:213px;width:104px">Save Progress</div>
<div class="rule"></div>

<div class="q-num">Q.5.</div>
<div class="q-text">What’s your knowledge regarding User Interface?</div>

<div class="option" style="top:318px"><div class="n">1</div>Lorem ipsum dolor sit amet, consecteteur adispiscing elit.</div>
<div class="option" style="top:380px"><div class="n">2</div>Lorem ipsum dolor sit amet, consecteteur adispiscing elit.</div>
<div class="option selected" style="top:441px"><div class="n">3</div>Lorem ipsum dolor sit amet, consecteteur adispiscing elit.</div>
<div class="option" style="top:503px"><div class="n">4</div>Lorem ipsum dolor sit amet, consecteteur adispiscing elit.</div>

<div class="progress-label"><svg width="8" height="10" viewBox="0 0 8 10" fill="none" stroke="#5d6166" stroke-width="1.4"><path d="M2 1l4 4-4 4"/></svg>Progress</div>
<svg class="abs" style="left:1050px;top:272px" width="32" height="32" viewBox="0 0 32 32"><circle cx="16" cy="16" r="13.5" fill="none" stroke="#e4e6e9" stroke-width="2.5"/><circle cx="16" cy="16" r="13.5" fill="none" stroke="#1aa6dc" stroke-width="2.5" stroke-dasharray="53 85" transform="rotate(-90 16 16)"/></svg>
<div class="count"><b>5</b> / 8</div>

<aside class="note">
  <h3>Note</h3>
  <p>Lorem ipsum dolor sit amet, consecteteur adispiscing elit. Lorem ipsum dolor sit amet, consecteteur adispiscing elit.Lorem ipsum dolor sit amet, consecteteur adispiscing elit.</p>
</aside>

<div class="percent">20<small>%</small></div>
<div class="track"></div>
<div class="fill"></div>

<div class="btn-outline" style="left:88px;top:722px;width:72px">Go Back</div>
<div class="skip">Skip <svg width="8" height="10" viewBox="0 0 8 10" fill="none" stroke="#5d6166" stroke-width="1.4"><path d="M2 1l4 4-4 4"/></svg></div>
<div class="btn-primary">Next</div>
</body>
</html>
```